Micro-Marketing and Vending Brochure

I am looking for an elegant, fun, eye catching brochure that will highlight my new business to protential clients in the Hotel, College/University and Hospital industry. please find pictures of Micro-Markets on line and on my website, to make a fun, professional and elegant design, use color scheme from website, and logo and a few picture will be attach to this email. This is a new business and i would like to represent my company in the best possible way, please take time with this project, color, front and wording is very important along with pics. I have a image of a micro-Market please take out the MURVO and place file logo of ZIRO..please let me know if more information is needed for this project to be successful

Industry/Entity Type

Business

```html
<!DOCTYPE html>
<html lang="en">
<head>
<meta charset="utf-8">
<title>Velta Micro-Market Brochure</title>
<link rel="stylesheet" href="https://fonts.googleapis.com/css2?family=Raleway:wght@400;500;700;800&display=swap">
<style>
  :root {
    --paper: #f2f2f4;
    --ink: #2b2b2b;
    --yellow: #fdd55a;
    --yellow-dark: #d6b04e;
    --purple: #b4a2cf;
    --purple-deep: #8a7a9c;
    --bullet: #8c7ea6;
    --sky-blue: #a9c6d6;
    --white: #ffffff;
  }
  html, body { margin: 0; padding: 0; overflow: hidden; }
  body { width: 1200px; height: 928px; background: var(--paper); }
  .brochure {
    position: relative; width: 1200px; height: 928px; overflow: hidden;
    font-family: "Raleway", Arial, sans-serif; color: var(--ink); background: var(--paper);
  }
  .backdrop { position: absolute; inset: 0; }
  .abs { position: absolute; margin: 0; }

  /* left panel */
  .head-band { left: 0; top: 0; width: 393px; height: 53px; background: var(--yellow); border-bottom: 5px solid var(--yellow-dark); }
  .head-band h2 { font-size: 24px; font-weight: 700; line-height: 53px; padding-left: 25px; margin: 0; }
  .audience { left: 25px; top: 79px; font-size: 16px; line-height: 20px; display: flex; gap: 14px; }
  .audience ul { list-style: none; margin: 0; padding: 0; }
  .benefits { left: 25px; top: 160px; width: 340px; list-style: none; padding: 0; font-size: 16px; line-height: 20px; }
  .benefits li { position: relative; padding-left: 34px; }
  .benefits li::before { content: ""; position: absolute; left: 2px; top: 4px; width: 12px; height: 11px; background: var(--bullet); }
  .intro { left: 25px; top: 260px; width: 344px; font-size: 16px; line-height: 20px; text-align: justify; }
  .sub-band { left: 0; top: 399px; width: 353px; height: 42px; background: var(--yellow); border-bottom: 4px solid var(--yellow-dark); }
  .sub-band h2 { font-size: 24px; font-weight: 700; line-height: 42px; padding-left: 26px; margin: 0; }
  .tech { left: 26px; top: 455px; width: 344px; font-size: 16px; line-height: 20px; text-align: justify; }

  /* middle panel */
  .mid-title { left: 394px; top: 50px; width: 403px; text-align: center; }
  .mid-title h1 { font-size: 45px; font-weight: 800; margin: 0; line-height: 48px; color: #333; letter-spacing: -0.5px; }
  .mid-title p { font-size: 18px; font-weight: 700; margin: 0; line-height: 20px; color: #333; }
  .mid-copy { left: 424px; top: 136px; width: 343px; font-size: 15.6px; line-height: 21px; text-align: justify; }
  .mid-copy p { margin: 0 0 14px; }
  .brand-mark { display: flex; align-items: center; gap: 12px; font-size: 52px; font-weight: 800; color: var(--white); letter-spacing: 2px; }
  .brand-dot { width: 54px; height: 54px; border-radius: 50%; background: var(--purple); }
  .mid-brand { left: 455px; top: 680px; }
  .contact { left: 556px; top: 760px; font-size: 15px; line-height: 19px; list-style: none; padding: 0; }
  .contact li { display: flex; align-items: center; gap: 14px; }
  .contact svg { width: 14px; height: 14px; }

  /* right panel */
  .front-brand { left: 860px; top: 20px; }
  .front-title { left: 797px; top: 460px; width: 403px; text-align: center; color: var(--white); }
  .front-title h1 { font-size: 56px; font-weight: 800; margin: 0; line-height: 60px; letter-spacing: -0.5px; }
  .front-title p { font-size: 22px; font-weight: 700; margin: 0; line-height: 24px; }
</style>
</head>
<body>
<main class="brochure">
  <svg class="backdrop" width="1200" height="928" viewBox="0 0 1200 928" aria-hidden="false">
    <defs>
      <linearGradient id="sky-field" x1="0" y1="0" x2="0" y2="1">
        <stop offset="0" stop-color="#d7e3ef"/>
        <stop offset="0.6" stop-color="#f4f6f7"/>
        <stop offset="0.8" stop-color="#e3ecd6"/>
        <stop offset="1" stop-color="#f2f2f4"/>
      </linearGradient>
      <linearGradient id="yoga-scene" x1="0" y1="0" x2="0" y2="1">
        <stop offset="0" stop-color="#2f86cf"/>
        <stop offset="0.55" stop-color="#cfe4f4"/>
        <stop offset="0.8" stop-color="#5bb33e"/>
        <stop offset="1" stop-color="#4aa233"/>
      </linearGradient>
    </defs>
    <rect x="394" y="0" width="403" height="520" fill="url(#sky-field)" role="img" aria-label="Soft sky over a green meadow with a tree"/>
    <polygon points="394,609 797,378 797,928 394,928" fill="var(--yellow)"/>
    <polygon points="0,606 293,771 0,928" fill="var(--sky-blue)"/>
    <polygon points="250,701 394,620 394,785" fill="var(--purple-deep)"/>
    <polygon points="797,0 1200,0 1200,300 932,452 797,378" fill="url(#yoga-scene)" role="img" aria-label="Photo of a woman in a yoga pose against blue sky and green grass"/>
    <polygon points="797,378 932,452 1200,300 1200,617 1094,557 797,723" fill="var(--purple)"/>
    <polygon points="797,723 1094,557 1200,617 1200,928 797,928" fill="var(--yellow)"/>
    <line x1="394" y1="0" x2="394" y2="928" stroke="#ffffff" stroke-width="1.5"/>
    <line x1="797" y1="0" x2="797" y2="928" stroke="#ffffff" stroke-width="1.5"/>
  </svg>

  <header class="abs head-band"><h2>Healthy, Happy Snack People</h2></header>
  <div class="abs audience"><span>FOR</span>
    <ul><li>a) Hotels</li><li>b) Colleges &amp;</li><li>c) Hospitals</li></ul>
  </div>
  <ul class="abs benefits">
    <li>Boost Employee/Clients/ patients Morale</li>
    <li>Increase Productivity</li>
    <li>Support employee Healthy lifestyle</li>
  </ul>
  <p class="abs intro">Velta Markets LLC Micro-Markets and Vending system allows you to select from hundreds of healthy, tasty and nutritional balance options. We have healthy snack and fresh produce</p>
  <div class="abs sub-band"><h2>Easy Convenient Healthy</h2></div>
  <p class="abs tech">Our Micro Markets are state of Art, with advance technology, credit card, debit card, self-check out Kiosk system, tracks calories and each item before purchase</p>

  <div class="abs mid-title"><h1>Micro-Market</h1><p>And Healthy Vending Solution</p></div>
  <div class="abs mid-copy">
    <p>Offering a large variety of healthy, nutritious products in an affordable and efficient manner. There is an increasing demand for products that suit a more healthier lifestyle, we understand those needs and strive for a wide selection of healthier types of products.</p>
    <p>Offering Special design solutions for Micro-Markets in Break-rooms, Office Buildings, Hotels and colleges hangout areas.</p>
  </div>
  <div class="abs brand-mark mid-brand"><span class="brand-dot"></span>VELTA</div>
  <ul class="abs contact">
    <li><svg viewBox="0 0 14 14"><rect x="3.5" y="0.5" width="7" height="13" rx="1.5" fill="none" stroke="#222" stroke-width="1.2"/><rect x="5.5" y="11" width="3" height="1" fill="#222"/></svg>(800) 555-0148</li>
    <li><svg viewBox="0 0 14 14"><circle cx="7" cy="7" r="6" fill="none" stroke="#222" stroke-width="1.2"/><line x1="1" y1="7" x2="13" y2="7" stroke="#222"/><ellipse cx="7" cy="7" rx="2.6" ry="6" fill="none" stroke="#222"/></svg>www.veltamarkets.com</li>
  </ul>

  <div class="abs brand-mark front-brand"><span class="brand-dot"></span>VELTA</div>
  <div class="abs front-title"><h1>Micro-Market</h1><p>And Healthy Vending Solution</p></div>
</main>
</body>
</html>
```